TLMWOS - Website Design

We require a WordPress website for an accounting firm.
Please review our concept design found on our development site:
http://quillmarsh.ca/tlmwoxe.
The client would like to carry the look and feel of the National Corporate site http://www.tlm.ca as well.
The site must be mobile ready (responsive)
The client will be providing a collection of staff photos for a contact page
Accounting

```html
<!DOCTYPE html>
<html lang="en">
<head>
<meta charset="utf-8">
<title>TLMWOS – Marlow Pine &amp; Associates</title>
<link rel="stylesheet" href="https://fonts.googleapis.com/css2?family=Open+Sans:wght@400;600;700&display=swap">
<style>
:root{
  --page:#e8e8e4;
  --header:#f7f7f5;
  --ink:#4a4a48;
  --muted:#6d6d6a;
  --nav-active:#5c6aa1;
  --olive:#8a8c48;
  --blue-head:#4f79a3;
  --news-title:#8a8a3a;
  --footer:#3a3c31;
  --footer-deep:#2c2e25;
  --footer-head:#c9c98a;
  --footer-text:#c8c8bc;
  --white:#ffffff;
  --rule:#d3d3cc;
}
*{margin:0;padding:0;box-sizing:border-box}
html,body{width:867px;height:1200px;overflow:hidden}
body{position:relative;background:var(--page);font-family:"Open Sans",Arial,sans-serif;color:var(--ink)}
.site-header{position:absolute;left:0;top:0;width:867px;height:43px;background:var(--header);border-bottom:1px solid var(--rule)}
.brand{position:absolute;left:52px;top:8px}
.brand-name{font-size:13px;font-weight:700;color:#3d3f5a;letter-spacing:.5px;line-height:15px;white-space:nowrap}
.brand-tag{font-size:7.5px;font-weight:700;color:#3d3f5a;letter-spacing:.6px;text-transform:uppercase;line-height:11px;white-space:nowrap}
.main-nav{position:absolute;right:52px;top:0;display:flex;height:43px}
.main-nav a{display:block;padding:0 14px;line-height:43px;font-size:8.5px;font-weight:600;color:var(--muted);text-decoration:none;letter-spacing:.6px}
.main-nav a.active{background:var(--nav-active);color:var(--white)}
.hero{position:absolute;left:0;top:43px;width:867px;height:430px;background:linear-gradient(120deg,#3b3f44 0%,#6b7077 35%,#9aa0a6 55%,#55595e 80%,#2d3035 100%)}
.welcome{position:absolute;left:52px;top:398px;width:763px;height:156px;background:var(--olive);padding:22px 40px;text-align:center;color:var(--white)}
.welcome h1{font-size:19px;font-weight:400;margin-bottom:10px}
.welcome p{font-size:9px;line-height:14px;color:#f1f1e6}
.services{position:absolute;left:52px;top:578px;width:511px}
.section-title{font-size:21px;font-weight:400;color:var(--blue-head);border-bottom:1px solid var(--rule);padding-bottom:6px;margin-bottom:10px}
.services-photo{width:511px;height:225px;background:linear-gradient(135deg,#8e8f86 0%,#c9c6bd 45%,#7d7f78 100%);margin-bottom:10px}
.services .intro{font-size:9px;line-height:14px;color:var(--muted);margin-bottom:10px}
.service-cols{display:flex;gap:20px}
.service-cols ul{list-style:none;flex:1}
.service-cols li{font-size:9px;line-height:17px;color:var(--ink);display:flex;align-items:center;gap:6px;white-space:nowrap}
.service-cols svg{flex:none}
.news{position:absolute;left:592px;top:578px;width:223px;height:467px;background:var(--white);border:1px solid var(--rule)}
.news .section-title{font-size:20px;color:var(--muted);background:#f1f1ee;padding:10px 12px;margin:0;border-bottom:1px solid var(--rule)}
.news-item{padding:12px 12px 10px;border-bottom:1px solid #ececE8}
.news-item h3{font-size:10.5px;font-weight:600;color:var(--news-title);line-height:14px}
.news-item time{display:block;font-size:8px;color:var(--muted);margin:4px 0}
.news-item p{font-size:8.5px;line-height:12px;color:var(--muted)}
.read-all{position:absolute;right:12px;bottom:12px;font-size:8px;font-weight:700;color:var(--ink);letter-spacing:.5px;text-decoration:none}
.site-footer{position:absolute;left:0;top:1060px;width:867px;height:122px;background:var(--footer);padding:12px 52px 0;display:flex;gap:28px}
.footer-col h4{font-size:8.5px;font-weight:700;color:var(--footer-head);letter-spacing:.8px;margin-bottom:6px;text-transform:uppercase}
.footer-col h5{font-size:8px;font-weight:600;color:var(--white);margin-bottom:2px;text-transform:uppercase}
.footer-col p,.footer-col li{font-size:8px;line-height:12px;color:var(--footer-text);list-style:none;white-space:nowrap}
.col-nav{width:150px}
.col-office{width:160px}
.social li{display:flex;align-items:center;gap:7px;margin-bottom:4px}
.social span.dot{width:12px;height:12px;border-radius:50%;background:var(--olive)}
.copyright{position:absolute;left:0;top:1182px;width:867px;height:18px;background:var(--footer-deep);text-align:center;font-size:7.5px;line-height:18px;color:#9c9c90}
</style>
</head>
<body>
<header class="site-header">
  <div class="brand">
    <div class="brand-name">MARLOW PINE &amp; ASSOCIATES</div>
    <div class="brand-tag">Chartered Professional Accountants</div>
  </div>
  <nav class="main-nav">
    <a class="active" href="#">HOME</a><a href="#">PROFILE</a><a href="#">CLIENT</a><a href="#">SERVICES</a><a href="#">RESOURCES</a><a href="#">CONTACT</a>
  </nav>
</header>

<div class="hero" role="img" aria-label="Photo of business colleagues reviewing financial charts at a desk"></div>

<section class="welcome">
  <h1>Welcome to TLMWOS Marlow Pine &amp; Associates Website</h1>
  <p>In addition to providing you with a portfolio of our firm and the services we provide, this website has been designed to become a helpful resource for you, our valued clients and visitors. Our dedication to our clients is what sets us apart, and we encourage you to contact us directly should you have any questions about your financial needs.</p>
</section>

<section class="services">
  <h2 class="section-title">Client Services</h2>
  <div class="services-photo" role="img" aria-label="Photo of an accounting team meeting around a table"></div>
  <p class="intro">Our firm offers a wide range of services to our individual and business clients. Our clients benefit from personalized, quality service that is beyond comparison. We have listed the services that we offer to our clients together with a brief description.</p>
  <div class="service-cols">
    <ul>
      <li><svg width="7" height="7" viewBox="0 0 7 7"><path d="M1 0l5 3.5L1 7z" fill="#8a8c48"/></svg>Accounting Services</li>
      <li><svg width="7" height="7" viewBox="0 0 7 7"><path d="M1 0l5 3.5L1 7z" fill="#8a8c48"/></svg>Financial Statements</li>
      <li><svg width="7" height="7" viewBox="0 0 7 7"><path d="M1 0l5 3.5L1 7z" fill="#8a8c48"/></svg>Bookkeeping/Write-Up</li>
      <li><svg width="7" height="7" viewBox="0 0 7 7"><path d="M1 0l5 3.5L1 7z" fill="#8a8c48"/></svg>Audit Services</li>
      <li><svg width="7" height="7" viewBox="0 0 7 7"><path d="M1 0l5 3.5L1 7z" fill="#8a8c48"/></svg>Reviews &amp; Compilations</li>
      <li><svg width="7" height="7" viewBox="0 0 7 7"><path d="M1 0l5 3.5L1 7z" fill="#8a8c48"/></svg>Tax Services</li>
      <li><svg width="7" height="7" viewBox="0 0 7 7"><path d="M1 0l5 3.5L1 7z" fill="#8a8c48"/></svg>Payroll Services</li>
    </ul>
    <ul>
      <li><svg width="7" height="7" viewBox="0 0 7 7"><path d="M1 0l5 3.5L1 7z" fill="#8a8c48"/></svg>Consulting Services</li>
      <li><svg width="7" height="7" viewBox="0 0 7 7"><path d="M1 0l5 3.5L1 7z" fill="#8a8c48"/></svg>Computer Consulting</li>
      <li><svg width="7" height="7" viewBox="0 0 7 7"><path d="M1 0l5 3.5L1 7z" fill="#8a8c48"/></svg>Business Succession Planning</li>
      <li><svg width="7" height="7" viewBox="0 0 7 7"><path d="M1 0l5 3.5L1 7z" fill="#8a8c48"/></svg>Accounting Software Selection &amp; Implementation</li>
      <li><svg width="7" height="7" viewBox="0 0 7 7"><path d="M1 0l5 3.5L1 7z" fill="#8a8c48"/></svg>Business Consulting</li>
      <li><svg width="7" height="7" viewBox="0 0 7 7"><path d="M1 0l5 3.5L1 7z" fill="#8a8c48"/></svg>Business Valuations</li>
      <li><svg width="7" height="7" viewBox="0 0 7 7"><path d="M1 0l5 3.5L1 7z" fill="#8a8c48"/></svg>Estate Planning</li>
    </ul>
  </div>
</section>

<aside class="news">
  <h2 class="section-title">Latest News</h2>
  <article class="news-item">
    <h3>Lorem ipsum dolor sit amet, consectetur adipiscing elit.</h3>
    <time>Apr 10, 2013</time>
    <p>Consectetuer adipiscing elit, sed diam nonummy nibh euismod tincidunt ut laoreet dolore magna.</p>
  </article>
  <article class="news-item">
    <h3>Lorem ipsum dolor sit amet, consectetur adipiscing elit.</h3>
    <time>Apr 10, 2013</time>
    <p>Consectetuer adipiscing elit, sed diam nonummy nibh euismod tincidunt ut laoreet dolore magna.</p>
  </article>
  <article class="news-item">
    <h3>Lorem ipsum dolor sit amet, consectetur adipiscing elit.</h3>
    <time>Apr 10, 2013</time>
    <p>Consectetuer adipiscing elit, sed diam nonummy nibh euismod tincidunt ut laoreet dolore magna.</p>
  </article>
  <a class="read-all" href="#">READ ALL NEWS</a>
</aside>

<footer class="site-footer">
  <div class="footer-col col-nav">
    <h4>Navigation</h4>
    <ul><li>Home</li><li>Profile</li><li>Client Services</li><li>Resources</li><li>Contact</li></ul>
  </div>
  <div class="footer-col col-office">
    <h4>Our Locations</h4>
    <h5>Harbourview Office</h5>
    <p>27 Lantern Court, Harbourview NB E3B 4K2<br>Phone 555 201 4410<br>Fax 555 201 4411<br>Toll Free 555 201 4412<br>Email info@marlowpine.ca</p>
  </div>
  <div class="footer-col col-office">
    <h4>&nbsp;</h4>
    <h5>Elmbrook Office</h5>
    <p>301 Quarry Road, Elmbrook NB E2V 1C7<br>Phone 555 388 2270<br>Fax 555 388 2271<br>Toll Free 555 388 2272<br>Email elmbrook@marlowpine.ca</p>
  </div>
  <div class="footer-col social">
    <h4>Our Locations</h4>
    <ul>
      <li><span class="dot"></span>Community</li>
      <li><span class="dot"></span>Updates</li>
      <li><span class="dot"></span>Network</li>
      <li><span class="dot"></span>Videos</li>
    </ul>
  </div>
</footer>
<div class="copyright">Copyright © 2013 Marlow Pine &amp; Associates. All Rights Reserved.</div>
</body>
</html>
```